Brightfield Homes needs a web design and brand identifier

Brightfield Homes is a pioneering approach by Victorian councils and four greenhouse alliances to support low income households to install solar systems with no upfront costs.

Brightfield Homes will commence in May 2017.

Brightfield Homes is looking for a designer to create a website banner incorporating a brand identifier for Brightfield Homes. The brand identifier will be used in Brightfield Homes promotional materials, such as flyers and mail outs.

The website banner and brand identifier should engender trust and confidence in the target group (retirees).

Reason: Hi, Thank you for your work so far. We've been given advice to get a separate logo designed (instead of trying to include this as part of the banner design). Sorry for not realising this until now - we're new to all this. So, I have a couple of preliminary logo designs that are being considered by our project control group. I will forward a copy of the logo once we have it. The project control group is looking for a web design that is unique to Brightfield Homes and a design that draws on the key elements of the program (i.e. it helps people save money and take control). The site should be friendly but not too informal as the target group is seniors. Here's a link to another community energy organisation: www.kindlewattnet.com.au/ Apologies again for the delays. Cheers, Doug

Target Market(s)

Home owning, low income, retirees

Industry/Entity Type

Non Profit

Number of Pages Required

1 page

Font styles to use
Sans Serif

Requirements
Must have
• Use of Brightfield Home name
• Must promote Brightfield Homes as safe, reliable and trustworthy
Nice to have
• Blue - to engender sense of safety and confidence (open to suggestions, though)
• Solar panels / the sun
Should not have
• Anything that is hard to read
• anything that promotes riskyness

```html
<!DOCTYPE html>
<html lang="en">
<head>
<meta charset="utf-8">
<title>Brightfield Homes</title>
<link href="https://fonts.googleapis.com/css2?family=Lato:wght@400;700;900&family=Open+Sans:wght@400;600;700&display=swap" rel="stylesheet">
<style>
:root{
  --blue:#3f6fcb;
  --blue-soft:#5a80d6;
  --ink:#1e1e1e;
  --text:#555a60;
  --muted:#7b8088;
  --line:#d9dce1;
  --white:#ffffff;
  --hero-a:#5d7fa6;
  --hero-b:#2e4a6e;
  --cta-a:#4b5560;
  --cta-b:#2d343b;
}
*{box-sizing:border-box;margin:0;padding:0}
html,body{width:1200px;height:2568px;overflow:hidden;background:var(--white)}
body{font-family:"Open Sans",Arial,sans-serif;color:var(--text);position:relative}
.abs{position:absolute}
h1,h2,h3,.brand{font-family:"Lato",Arial,sans-serif}

/* header */
.site-header{position:absolute;left:0;top:0;width:1200px;height:88px;border-top:4px solid var(--blue);background:var(--white)}
.brand{position:absolute;display:flex;align-items:center;gap:12px;font-weight:900;color:var(--ink);font-size:23px;letter-spacing:.3px}
.brand-mark{width:30px;height:30px;background:var(--blue)}
.header-brand{left:98px;top:28px}
.contact-bar{position:absolute;right:98px;top:14px;display:flex;gap:28px;font-size:15px;color:var(--ink);font-weight:600}
.contact-bar span{display:flex;align-items:center;gap:10px}
.main-nav{position:absolute;right:96px;top:56px;display:flex;gap:30px;font-size:14.5px;font-weight:600;color:var(--ink);align-items:center}
.main-nav .active{color:var(--blue)}

/* hero */
.hero{position:absolute;left:0;top:88px;width:1200px;height:449px;background:linear-gradient(100deg,var(--hero-a) 0%,#6f8fb3 40%,var(--hero-b) 100%)}
.hero h1{position:absolute;left:98px;top:98px;font-size:64px;font-weight:900;color:var(--white);letter-spacing:1px}
.hero p{position:absolute;left:98px;top:185px;width:590px;font-size:17.5px;line-height:30px;color:var(--white)}
.btn-outline-light{position:absolute;left:98px;top:297px;width:170px;height:40px;border:2px solid var(--white);border-radius:22px;color:var(--white);font-weight:700;font-size:14px;display:flex;align-items:center;justify-content:center}
.slider-dots{position:absolute;left:565px;top:390px;display:flex;gap:4px}
.slider-dots i{width:14px;height:14px;border:2px solid var(--white);border-radius:50%}
.slider-dots i:first-child{background:var(--blue)}

/* welcome */
.welcome h2{position:absolute;left:0;width:1200px;top:590px;text-align:center;font-size:26px;font-weight:900;color:var(--ink)}
.welcome p{position:absolute;left:225px;width:750px;top:642px;text-align:center;font-size:12.5px;line-height:25px;color:var(--text)}
.feature{position:absolute;top:728px;width:150px;text-align:center}
.feature-circle{width:150px;height:150px;border:1.5px solid #3a3a3a;border-radius:50%;display:flex;align-items:center;justify-content:center}
.feature-label{margin-top:28px;font-family:"Lato",Arial,sans-serif;font-weight:700;font-size:19px;color:var(--ink);width:220px;margin-left:-35px}

/* how it works */
.how{position:absolute;left:0;top:985px;width:1200px;height:512px}
.how-panel{position:absolute;left:0;top:0;width:600px;height:512px;background:var(--blue-soft)}
.how-photo{position:absolute;left:600px;top:0;width:600px;height:512px;background:linear-gradient(135deg,#b9c8c2 0%,#d9dcd2 45%,#8aa26a 100%)}
.how h2{position:absolute;left:98px;top:42px;font-size:25px;font-weight:900;color:var(--white)}
.step{position:absolute;left:98px;display:flex;align-items:center;gap:28px;color:var(--white);font-size:13.5px;line-height:24px;width:470px}
.step-num{flex:none;width:64px;height:64px;border:2.5px solid var(--white);border-radius:50%;display:flex;align-items:center;justify-content:center;font-family:"Lato",Arial,sans-serif;font-size:26px;font-weight:700}
.step-num.current{background:var(--white);color:var(--blue)}

/* news + why */
.section-title{position:absolute;top:1552px;font-size:25px;font-weight:900;color:var(--ink)}
.news-item{position:absolute;left:98px;width:480px;display:flex;gap:28px}
.news-thumb{flex:none;width:152px;height:112px;border:3px solid var(--white);box-shadow:0 0 0 1px var(--line)}
.news-item h3{font-size:16px;font-weight:700;line-height:26px;color:var(--ink);margin-top:4px}
.news-meta{margin-top:10px;font-size:12.5px;color:var(--muted);display:flex;gap:10px;align-items:center}
.news-meta span{display:flex;align-items:center;gap:6px}
.link-more{position:absolute;font-size:12.5px;font-weight:700;color:var(--blue)}
.why-intro{position:absolute;left:645px;top:1600px;font-size:12px;font-weight:600;color:var(--ink)}
.why-list{position:absolute;left:645px;top:1640px;list-style:none}
.why-list li{display:flex;align-items:center;gap:12px;font-size:12px;color:var(--text);height:33.5px}
.btn-outline{position:absolute;left:645px;top:1861px;width:132px;height:34px;border:1.5px solid #9aa0a8;border-radius:18px;font-size:12px;font-weight:700;color:var(--blue);display:flex;align-items:center;justify-content:center}

/* call to action */
.cta{position:absolute;left:0;top:1960px;width:1200px;height:262px;background:linear-gradient(100deg,var(--cta-a),#5d6670 50%,var(--cta-b))}
.cta p{position:absolute;left:150px;width:900px;top:54px;text-align:center;font-family:"Lato",Arial,sans-serif;font-weight:700;font-size:23px;line-height:36px;color:var(--white)}
.btn-solid{position:absolute;left:492px;top:155px;width:216px;height:46px;border:2px solid var(--white);border-radius:24px;background:var(--blue);color:var(--white);font-weight:700;font-size:15px;display:flex;align-items:center;justify-content:center}

/* footer */
.footer-brand{left:98px;top:2358px;font-size:24px}
.footer-brand .brand-mark{width:32px;height:32px}
.footer-col{position:absolute;top:2276px}
.footer-col h3{font-size:17px;font-weight:700;color:var(--ink);margin-bottom:20px}
.footer-links{list-style:none;font-size:12px;color:var(--text);line-height:22px}
.newsletter p{font-size:12px;line-height:20px;color:var(--text);width:210px}
.email-field{margin-top:14px;width:254px;border-bottom:1px solid var(--line);font-size:12px;color:#9aa0a8;padding:4px 12px 8px}
.btn-subscribe{margin-top:14px;width:96px;height:30px;border:1.5px solid #9aa0a8;border-radius:16px;font-size:11px;font-weight:700;color:var(--blue);display:flex;align-items:center;justify-content:center}
.contact-list{list-style:none;font-size:12px;color:var(--text)}
.contact-list li{display:flex;gap:18px;line-height:18px;margin-bottom:14px}
.contact-list svg{flex:none;margin-top:2px}
.footer-rule{position:absolute;left:98px;top:2493px;width:1004px;height:1px;background:var(--line)}
.copyright{position:absolute;left:98px;top:2521px;font-size:11px;color:var(--text)}
.social{position:absolute;left:975px;top:2512px;display:flex;gap:8px}
.social i{width:26px;height:26px;border:1.5px solid #9aa0a8;border-radius:50%}
</style>
</head>
<body>

<header class="site-header">
  <div class="brand header-brand"><span class="brand-mark"></span>BRIGHTFIELD HOMES</div>
  <div class="contact-bar">
    <span><svg width="16" height="16" viewBox="0 0 24 24"><path fill="#3f6fcb" d="M6.6 10.8c1.4 2.8 3.8 5.1 6.6 6.6l2.2-2.2c.3-.3.7-.4 1-.2 1.1.4 2.3.6 3.6.6.6 0 1 .4 1 1V20c0 .6-.4 1-1 1C10.6 21 3 13.4 3 4c0-.6.4-1 1-1h3.5c.6 0 1 .4 1 1 0 1.3.2 2.5.6 3.6.1.3 0 .7-.2 1z"/></svg>0400 555 271</span>
    <span><svg width="18" height="14" viewBox="0 0 18 14"><rect width="18" height="14" rx="1.5" fill="#3f6fcb"/><path d="M1 1.5l8 6 8-6" stroke="#fff" stroke-width="1.6" fill="none"/></svg>hello@brightfieldhomes.org</span>
  </div>
  <nav class="main-nav">
    <span class="active">HOME</span><span>ABOUT US</span><span>SERVICES</span><span>GO SOLAR</span><span>NEWS</span><span>CONTACT US</span>
    <svg width="15" height="15" viewBox="0 0 16 16"><circle cx="6.5" cy="6.5" r="5" stroke="#1e1e1e" stroke-width="2" fill="none"/><path d="M10.3 10.3L15 15" stroke="#1e1e1e" stroke-width="2.4"/></svg>
  </nav>
</header>

<section class="hero" role="img" aria-label="Photo of a blue weatherboard house with a roof covered in solar panels under a clear sky">
  <h1>BRIGHTFIELD HOMES</h1>
  <p>We are started in support with Victorian councils and four greenhouse alliances to support low income households to install solar systems with no upfront costs.</p>
  <div class="btn-outline-light">GET INVOLVED</div>
  <div class="slider-dots"><i></i><i></i><i></i><i></i></div>
</section>

<section class="welcome">
  <h2>WELCOME TO BRIGHTFIELD HOMES</h2>
  <p>Brightfield Homes is a pioneering approach by Victorian councils to support pensioner households to install solar with no upfront costs. We've done the hard work of finding a safe, reliable and quality installer so pensioners don't have to.</p>

  <div class="feature" style="left:150px">
    <div class="feature-circle"><svg width="76" height="48" viewBox="0 0 76 48"><rect x="2" y="2" width="72" height="44" rx="3" fill="#3f6fcb"/><rect x="9" y="8" width="58" height="32" rx="2" fill="none" stroke="#fff" stroke-width="2.5"/><circle cx="38" cy="24" r="11" fill="#fff"/><text x="38" y="30" text-anchor="middle" font-family="Lato,Arial,sans-serif" font-weight="900" font-size="16" fill="#3f6fcb">1</text></svg></div>
    <div class="feature-label">No upfront costs</div>
  </div>
  <div class="feature" style="left:400px">
    <div class="feature-circle"><svg width="46" height="58" viewBox="0 0 46 58"><path d="M11 26V17a12 12 0 0 1 24 0v9" stroke="#3f6fcb" stroke-width="6" fill="none"/><rect x="2" y="24" width="42" height="32" rx="4" fill="#3f6fcb"/></svg></div>
    <div class="feature-label">Safe</div>
  </div>
  <div class="feature" style="left:649px">
    <div class="feature-circle"><svg width="50" height="60" viewBox="0 0 50 60"><path d="M2 4h46v22c0 16-11 27-23 32C13 53 2 42 2 26z" fill="#3f6fcb"/><path d="M25 10h16v16c0 11-7 19-16 23z" fill="#fff"/></svg></div>
    <div class="feature-label">Reliable</div>
  </div>
  <div class="feature" style="left:899px">
    <div class="feature-circle"><svg width="64" height="60" viewBox="0 0 64 60"><rect x="2" y="26" width="13" height="32" rx="2" fill="#3f6fcb"/><path d="M20 28l12-16c2-3 3-7 3-10 4 0 7 4 6 9l-2 11h17c4 0 6 4 5 7l-5 23c-1 3-3 6-7 6H20z" fill="#3f6fcb"/></svg></div>
    <div class="feature-label">Trustworthy</div>
  </div>
</section>

<section class="how">
  <div class="how-panel"></div>
  <div class="how-photo" role="img" aria-label="Photo of a smiling retired couple standing outside their home among trees"></div>
  <h2>HOW IT WORKS?</h2>
  <div class="step" style="top:106px"><span class="step-num current">1</span>Brightfield Homes checks that every person gets a solar system that pays for itself in energy savings from day one</div>
  <div class="step" style="top:204px"><span class="step-num">2</span>Brightfield Homes organises for the solar system to be installed</div>
  <div class="step" style="top:299px"><span class="step-num">3</span>Brightfield Homes supports pensioners to understand and get the most out of solar</div>
  <div class="step" style="top:394px"><span class="step-num">4</span>Pensioners gradually pay for cost through their usual rates payments at 0% interest</div>
</section>

<section class="news">
  <h2 class="section-title" style="left:98px">LATEST NEWS</h2>
  <article class="news-item" style="top:1612px">
    <div class="news-thumb" role="img" aria-label="Photo of an installer in a hard hat fitting solar panels" style="background:linear-gradient(135deg,#6f9bd8,#2f5fa8 60%,#d9c27a)"></div>
    <div>
      <h3>At vero eos et accusamus et iusto odio dignissimos ducimus qui blan</h3>
      <div class="news-meta"><span><svg width="12" height="12" viewBox="0 0 12 12"><rect x="1" y="2" width="10" height="9" rx="1" fill="#3f6fcb"/><rect x="2" y="5" width="8" height="5" fill="#fff"/></svg>02/03/2017</span>|<span><svg width="11" height="12" viewBox="0 0 11 12"><circle cx="5.5" cy="3.5" r="3" fill="#3f6fcb"/><path d="M0 12c0-4 2.5-5.5 5.5-5.5S11 8 11 12z" fill="#3f6fcb"/></svg>Admin</span></div>
    </div>
  </article>
  <article class="news-item" style="top:1750px">
    <div class="news-thumb" role="img" aria-label="Photo of a red tiled house roof fitted with solar panels" style="background:linear-gradient(180deg,#8fb0d8,#3d5f8f 45%,#b5583f 75%,#6f8f4e)"></div>
    <div>
      <h3>At vero eos et accusamus et iusto odio dignissimos ducimus qui blan</h3>
      <div class="news-meta"><span><svg width="12" height="12" viewBox="0 0 12 12"><rect x="1" y="2" width="10" height="9" rx="1" fill="#3f6fcb"/><rect x="2" y="5" width="8" height="5" fill="#fff"/></svg>02/03/2017</span>|<span><svg width="11" height="12" viewBox="0 0 11 12"><circle cx="5.5" cy="3.5" r="3" fill="#3f6fcb"/><path d="M0 12c0-4 2.5-5.5 5.5-5.5S11 8 11 12z" fill="#3f6fcb"/></svg>Admin</span></div>
    </div>
  </article>
  <span class="link-more" style="left:98px;top:1884px">VIEW MORE &gt;&gt;</span>
</section>

<section class="why">
  <h2 class="section-title" style="left:645px">WHY CHOOSE BRIGHTFIELD HOMES?</h2>
  <p class="why-intro">Brightfield Homes will support councils to install solar for pension card households by:</p>
  <ul class="why-list">
    <li><svg width="12" height="12" viewBox="0 0 12 12"><circle cx="6" cy="6" r="6" fill="#3f6fcb"/><path d="M3 6.2l2 2 4-4" stroke="#fff" stroke-width="1.6" fill="none"/></svg>Coordinating household promotion and recruitment</li>
    <li><svg width="12" height="12" viewBox="0 0 12 12"><circle cx="6" cy="6" r="6" fill="#3f6fcb"/><path d="M3 6.2l2 2 4-4" stroke="#fff" stroke-width="1.6" fill="none"/></svg>Responding to householder enquiries</li>
    <li><svg width="12" height="12" viewBox="0 0 12 12"><circle cx="6" cy="6" r="6" fill="#3f6fcb"/><path d="M3 6.2l2 2 4-4" stroke="#fff" stroke-width="1.6" fill="none"/></svg>Managing the procurement process to contract a solar installer</li>
    <li><svg width="12" height="12" viewBox="0 0 12 12"><circle cx="6" cy="6" r="6" fill="#3f6fcb"/><path d="M3 6.2l2 2 4-4" stroke="#fff" stroke-width="1.6" fill="none"/></svg>Administering the installations</li>
    <li><svg width="12" height="12" viewBox="0 0 12 12"><circle cx="6" cy="6" r="6" fill="#3f6fcb"/><path d="M3 6.2l2 2 4-4" stroke="#fff" stroke-width="1.6" fill="none"/></svg>Securing lower interest finance options for households</li>
    <li><svg width="12" height="12" viewBox="0 0 12 12"><circle cx="6" cy="6" r="6" fill="#3f6fcb"/><path d="M3 6.2l2 2 4-4" stroke="#fff" stroke-width="1.6" fill="none"/></svg>Evaluating the project</li>
  </ul>
  <div class="btn-outline">READ MORE &gt;&gt;</div>
</section>

<section class="cta" role="img" aria-label="Close-up photo of a hand on rows of dark solar panels">
  <p>Over 20 Victorian councils have come together with support from the State Government's Clean Power Works Fund to run the Brightfield Home program.</p>
  <div class="btn-solid">GET INVOLVED</div>
</section>

<footer>
  <div class="brand footer-brand"><span class="brand-mark"></span>BRIGHTFIELD HOMES</div>
  <div class="footer-col" style="left:426px">
    <h3>Information</h3>
    <ul class="footer-links"><li>Home</li><li>About us</li><li>Services</li><li>Go Solar</li><li>News</li><li>Contact US</li></ul>
  </div>
  <div class="footer-col newsletter" style="left:606px">
    <h3>Newsletter Subscription</h3>
    <p>Register your Email Address to get Information about us</p>
    <div class="email-field">Email Address</div>
    <div class="btn-subscribe">SUBSCRIBE</div>
  </div>
  <div class="footer-col" style="left:907px">
    <h3>Contact Us</h3>
    <ul class="contact-list">
      <li><svg width="10" height="14" viewBox="0 0 10 14"><path d="M5 0a5 5 0 0 1 5 5c0 4-5 9-5 9S0 9 0 5a5 5 0 0 1 5-5z" fill="#3f6fcb"/><circle cx="5" cy="5" r="2" fill="#fff"/></svg>12 Larkin Way, Elmvale VIC 3999,<br>Australia</li>
      <li><svg width="12" height="12" viewBox="0 0 24 24"><path fill="#3f6fcb" d="M6.6 10.8c1.4 2.8 3.8 5.1 6.6 6.6l2.2-2.2c.3-.3.7-.4 1-.2 1.1.4 2.3.6 3.6.6.6 0 1 .4 1 1V20c0 .6-.4 1-1 1C10.6 21 3 13.4 3 4c0-.6.4-1 1-1h3.5c.6 0 1 .4 1 1 0 1.3.2 2.5.6 3.6.1.3 0 .7-.2 1z"/></svg>0400 555 271</li>
      <li><svg width="12" height="12" viewBox="0 0 12 12"><rect x="2" y="0" width="8" height="4" fill="#3f6fcb"/><rect x="0" y="4" width="12" height="6" rx="1" fill="#3f6fcb"/><rect x="3" y="7" width="6" height="5" fill="#3f6fcb" stroke="#fff"/></svg>1 800 555 0142</li>
      <li><svg width="13" height="10" viewBox="0 0 18 14"><rect width="18" height="14" rx="1.5" fill="#3f6fcb"/><path d="M1 1.5l8 6 8-6" stroke="#fff" stroke-width="1.6" fill="none"/></svg>hello@brightfieldhomes.org</li>
    </ul>
  </div>
  <div class="footer-rule"></div>
  <p class="copyright">Copyrights © 2017, Brightfield Homes. All rights reserved.</p>
  <div class="social"><i></i><i></i><i></i><i></i></div>
</footer>

</body>
</html>
```